Chimney Service company needs new business card design

We need a updated business card with our new logo added. We provide a full range of chimney services throughout Vermont and New Hampshire. The business card will be one sided and color. Attached is our current business card another document showing all the information we would like on the card.
We dont like a lot of flashy colors.... here is a link to our website to get an idea of our branding www.flueguardianvt.example

Target Market(s)

homeowners

Industry/Entity Type

Business

Contact Information for Business Card

See attached sheet for content.

Font styles to use
Serif
Sans Serif

Requirements
Must have
• all information provided on separate sheet
Should not have
• Additional information that may clogg up design

```html
<!DOCTYPE html>
<html lang="en">
<head>
<meta charset="utf-8">
<title>Flue Guardian – Business Card</title>
<link rel="stylesheet" href="https://fonts.googleapis.com/css2?family=Cinzel:wght@400;600&family=Montserrat:wght@400;600&display=swap">
<style>
  :root {
    --stage: #2b2b2b;
    --brand-red: #a11c22;
    --ink: #2d2d2d;
    --paper: #ffffff;
    --paper-on-red: #ffffff;
  }
  * { box-sizing: border-box; margin: 0; padding: 0; }
  html, body { width: 1200px; height: 738px; overflow: hidden; }
  body {
    background: var(--stage);
    display: flex;
    align-items: center;
    justify-content: center;
    gap: 40px;
    font-family: "Montserrat", sans-serif;
  }
  .card {
    width: 520px;
    height: 297px;
    position: relative;
    box-shadow: 0 10px 30px rgba(0,0,0,.5);
  }
  .brand-name {
    font-family: "Cinzel", serif;
    font-weight: 400;
    letter-spacing: 1px;
    line-height: 1;
    white-space: nowrap;
  }

  /* Back side */
  .card--back { background: var(--brand-red); color: var(--paper-on-red); }
  .card--back .brand-name {
    position: absolute; left: 0; right: 0; top: 112px;
    text-align: center;
    font-size: 32px;
  }
  .back-tagline {
    position: absolute; left: 0; right: 0; bottom: 36px;
    text-align: center;
    font-family: "Cinzel", serif; font-size: 12.5px; letter-spacing: .5px;
  }

  /* Front side */
  .card--front { background: var(--paper); color: var(--ink); }
  .card--front .brand-name {
    position: absolute; left: 20px; top: 124px; width: 250px;
    text-align: center;
    font-size: 23px;
  }
  .divider {
    position: absolute; left: 282px; top: 50px;
    width: 2px; height: 150px; background: var(--brand-red);
  }
  .contact {
    position: absolute; left: 298px; top: 46px;
    list-style: none; font-size: 11px; line-height: 16px;
  }
  .contact li { display: flex; align-items: center; gap: 8px; }
  .contact svg { width: 10px; height: 10px; fill: var(--brand-red); flex: none; }
  .services { position: absolute; left: 300px; top: 110px; }
  .services h2 {
    font-family: "Cinzel", serif; font-weight: 600;
    color: var(--brand-red); font-size: 14px; margin-bottom: 3px;
  }
  .services ul { list-style: none; font-size: 11px; line-height: 15px; }
  .service-area {
    position: absolute; left: 0; right: 0; bottom: 34px;
    text-align: center;
    font-family: "Cinzel", serif; font-size: 13px;
  }
  .service-area .since { font-family: "Montserrat", sans-serif; color: var(--brand-red); font-size: 12px; }
</style>
</head>
<body>
  <section class="card card--back">
    <div class="brand-name">FLUE GUARDIAN</div>
    <p class="back-tagline">Fully Insured–Free Estimates | Family Owned and Operated</p>
  </section>

  <section class="card card--front">
    <div class="brand-name">FLUE GUARDIAN</div>
    <span class="divider"></span>
    <ul class="contact">
      <li><svg viewBox="0 0 10 10"><path d="M2 0l2 2.5-1.2 1.2a6 6 0 0 0 3.5 3.5L7.5 6 10 8 8.5 10C4 10 0 6 0 1.5z"/></svg>802-555-0147</li>
      <li><svg viewBox="0 0 10 10"><path d="M0 2h10v6H0zM0 2l5 3.5L10 2" stroke="#fff" stroke-width=".8"/></svg>info@flueguardianvt.example</li>
      <li><svg viewBox="0 0 10 10"><circle cx="5" cy="5" r="4.5" fill="none" stroke="#a11c22"/><path d="M0.5 5h9M5 .5v9" stroke="#a11c22" stroke-width=".8"/></svg>www.flueguardianvt.example</li>
    </ul>
    <div class="services">
      <h2>SERVICES WE PROVIDE</h2>
      <ul>
        <li>Full Masonry Services</li>
        <li>Historic chimney restoration</li>
        <li>Stainless steel liners</li>
        <li>New Chimney installations</li>
        <li>Fully Certified Chimney sweeps</li>
      </ul>
    </div>
    <p class="service-area">SERVING VT AND NEW HAMPSHIRE-<span class="since">since 1989</span></p>
  </section>
</body>
</html>
```